Business Card - MARLOW Real Estate

Design a professional business card for a real estate agent.

Target Market(s)

Residential property and home owners in the middle suburban eastern suburbs of Melbourne, Australia. Property prices range between $1m and $3m in value.

Industry/Entity Type

Real Estate

Contact Information for Business Card

FRONT: Black on White
MARLOW Real Estate logo
Felix Tarrant
Director / Officer in Effective Control / CEA PLKT
47 Quarry Lane,
Brindle Heights VIC 3987
Tel: 1800 562 907
Mob: 0488 216 740
E: felix@marlowrealestate-example.com.au
W. www.marlowrealestate-example.com.au

BACK: White on Black logo
MARLOW Real Estate logo
website: www.marlowrealestate-example.com.au

Colors
ffffff
000000

Requirements
Must have
• Detail as specified above
• White on black for front
• Black on white for back
Nice to have
• I may like to integrate my photo on the card;
• there will be other agents also requiring the card so a template would be useful
Should not have
• animations / drawings

```html
<!DOCTYPE html>
<html lang="en">
<head>
<meta charset="UTF-8">
<title>MARLOW Real Estate – Business Card</title>
<link rel="stylesheet" href="https://fonts.googleapis.com/css2?family=Montserrat:wght@600;700&family=Questrial&display=swap">
<style>
  :root {
    --ink: #231f20;
    --paper: #ffffff;
    --canvas: #e4e6ea;
    --photo-light: #d9d9dc;
    --photo-dark: #2a2a2e;
  }
  * { margin: 0; padding: 0; box-sizing: border-box; }
  html, body { width: 1200px; height: 810px; overflow: hidden; }
  body {
    background: var(--canvas);
    position: relative;
    font-family: "Questrial", "Century Gothic", sans-serif;
    color: var(--ink);
  }
  .card {
    position: absolute;
    left: 280px;
    width: 640px;
    height: 366px;
    overflow: hidden;
    box-shadow: 0 4px 14px rgba(0,0,0,0.18);
  }
  .card--back { top: 24px; background: var(--ink); }
  .card--front { top: 420px; background: var(--paper); }

  .wordmark { font-family: "Montserrat", sans-serif; font-weight: 700; line-height: 1; }
  .tagline { font-family: "Questrial", sans-serif; text-transform: uppercase; line-height: 1; }

  .back-logo {
    position: absolute;
    left: 0; right: 0;
    top: 118px;
    text-align: center;
    color: var(--paper);
  }
  .back-logo .wordmark { font-size: 84px; letter-spacing: 2px; }
  .back-logo .tagline { font-size: 17px; letter-spacing: 22px; margin-top: 16px; padding-left: 22px; }

  .agent-photo {
    position: absolute;
    left: 44px; top: 28px;
    width: 180px; height: 301px;
    background: linear-gradient(180deg, var(--photo-light) 0%, var(--photo-dark) 25%, var(--photo-dark) 100%);
    border-radius: 60px 60px 0 0;
  }
  .footer-band { position: absolute; left: 0; bottom: 0; }

  .details {
    position: absolute;
    right: 78px;
    top: 48px;
    text-align: right;
  }
  .front-logo .wordmark { font-size: 40px; letter-spacing: 1px; }
  .front-logo .tagline { font-size: 9px; letter-spacing: 7px; margin-top: 6px; margin-right: -7px; }
  .agent-name {
    font-family: "Montserrat", sans-serif;
    font-weight: 700;
    font-size: 23px;
    margin-top: 24px;
    line-height: 1.1;
  }
  .agent-role { font-size: 15px; line-height: 1.2; }

  .contact-list { position: absolute; right: 60px; top: 188px; list-style: none; }
  .contact-item {
    display: flex;
    justify-content: flex-end;
    align-items: flex-start;
    gap: 10px;
    font-size: 14px;
    line-height: 17px;
    margin-bottom: 14px;
    text-align: right;
  }
  .contact-item svg { width: 15px; height: 15px; flex: none; margin-top: 2px; fill: var(--ink); }
</style>
</head>
<body>

  <section class="card card--back" aria-label="Business card back">
    <div class="back-logo">
      <div class="wordmark">MARLOW</div>
      <div class="tagline">Real Estate</div>
    </div>
  </section>

  <section class="card card--front" aria-label="Business card front">
    <div class="agent-photo" role="img" aria-label="Portrait photo of Felix Tarrant in a dark suit"></div>

    <svg class="footer-band" width="295" height="36" viewBox="0 0 295 36" aria-hidden="true">
      <polygon points="0,0 262,0 295,36 0,36" fill="var(--ink)"/>
    </svg>

    <div class="details">
      <div class="front-logo">
        <div class="wordmark">MARLOW</div>
        <div class="tagline">Real Estate</div>
      </div>
      <div class="agent-name">Felix Tarrant</div>
      <div class="agent-role">Director</div>
    </div>

    <ul class="contact-list">
      <li class="contact-item">
        <span>47 Quarry Lane,<br>Brindle Heights VIC 3987</span>
        <svg viewBox="0 0 24 24" aria-hidden="true"><path d="M12 2a7 7 0 0 0-7 7c0 5 7 13 7 13s7-8 7-13a7 7 0 0 0-7-7zm0 9.5A2.5 2.5 0 1 1 12 6.5a2.5 2.5 0 0 1 0 5z"/></svg>
      </li>
      <li class="contact-item">
        <span>1800 562 907<br>0488 216 740</span>
        <svg viewBox="0 0 24 24" aria-hidden="true"><path d="M6.6 10.8a15.1 15.1 0 0 0 6.6 6.6l2.2-2.2a1 1 0 0 1 1-.25 11.4 11.4 0 0 0 3.6.57 1 1 0 0 1 1 1V20a1 1 0 0 1-1 1A17 17 0 0 1 3 4a1 1 0 0 1 1-1h3.5a1 1 0 0 1 1 1c0 1.25.2 2.45.57 3.57a1 1 0 0 1-.25 1z"/></svg>
      </li>
      <li class="contact-item">
        <span>felix@marlowrealestate-example.com.au<br>www.marlowrealestate-example.com.au</span>
        <svg viewBox="0 0 24 24" aria-hidden="true"><path d="M12 2a10 10 0 1 0 0 20 10 10 0 0 0 0-20zm-1 17.9A8 8 0 0 1 4.1 10.6L9 15.5v1a2 2 0 0 0 2 2zm6.9-2.5a2 2 0 0 0-1.9-1.4h-1v-3a1 1 0 0 0-1-1H8v-2h2a1 1 0 0 0 1-1V7h2a2 2 0 0 0 2-2v-.4a8 8 0 0 1 2.9 12.8z"/></svg>
      </li>
    </ul>
  </section>

</body>
</html>
```